Business Card for a mobile physiotherapy company

I need a layout for a business card for a mobile physiotherapy company.
Slogan is "Mobile Physiotherapy - Your Road To Recovery"
Phone number is 867-555-0142
Email VardenTherapy@postnest.ca (subject to change with website)
Website www.VardenTherapy.ca
My name and credentials: Luke Varden Luke Varden, BSc(kin), MPT, CAFCI, IMS
Information maybe included: Direct Billing, Services including Physiotherapy, IMS, acupuncture
Maybe include facebook and instagram logos
One side with the logo clean and sharp
Other side with details, try not to look too busy, keep everything concise

```html
<!DOCTYPE html>
<html lang="en">
<head>
<meta charset="utf-8">
<title>Varden Therapy – Business Card</title>
<link rel="stylesheet" href="https://fonts.googleapis.com/css2?family=Bebas+Neue&family=Lato:wght@400;700&display=swap">
<style>
  :root {
    --navy: #29456b;
    --paper: #f3f3f3;
    --grey-text: #7a7a7a;
    --backdrop: #5f5249;
    --white: #ffffff;
  }
  * { margin: 0; padding: 0; box-sizing: border-box; }
  html, body {
    width: 1200px; height: 960px; overflow: hidden;
    background: var(--backdrop);
    font-family: "Lato", Arial, sans-serif;
  }
  .card {
    position: absolute; left: 296px; width: 614px; height: 351px;
  }
  .card--front {
    top: 104px; background: var(--navy);
    display: flex; flex-direction: column; align-items: center; justify-content: center;
  }
  .brand-name {
    font-family: "Lato", Arial, sans-serif; font-weight: 700; color: var(--white);
    text-align: center; line-height: 1;
  }
  .brand-name__main { display: block; font-size: 50px; letter-spacing: 3px; }
  .brand-name__sub { display: block; font-size: 22px; letter-spacing: 9px; margin-top: 14px; }

  .card--back { top: 508px; background: var(--paper); }
  .holder {
    position: absolute; right: 354px; top: 152px; text-align: right;
  }
  .holder__name {
    font-family: "Bebas Neue", Impact, sans-serif; font-size: 31px;
    color: var(--navy); line-height: 1; letter-spacing: 0.3px;
  }
  .holder__credentials { font-size: 14px; color: var(--grey-text); margin-top: 2px; }
  .divider {
    position: absolute; left: 306px; top: 105px; width: 1.5px; height: 140px;
    background: var(--navy);
  }
  .services {
    position: absolute; left: 344px; top: 107px; list-style: none;
    font-size: 14px; color: var(--grey-text); line-height: 18px;
  }
  .dot { color: var(--navy); }
  .contacts {
    position: absolute; left: 344px; top: 174px; list-style: none;
    font-size: 14px; color: var(--grey-text); line-height: 17.7px;
  }
  .contacts li { display: flex; align-items: center; gap: 8px; }
  .contacts svg { width: 11px; height: 11px; flex: none; }
  .social-dot { width: 10px; height: 10px; border-radius: 50%; background: var(--navy); display: inline-block; }
  .slogan-band {
    position: absolute; left: 0; bottom: 0; width: 100%; height: 28px;
    background: var(--navy); color: var(--white);
    font-size: 14px; text-align: center; line-height: 28px;
  }
</style>
</head>
<body>
  <section class="card card--front">
    <h1 class="brand-name">
      <span class="brand-name__main">VARDEN</span>
      <span class="brand-name__sub">THERAPY</span>
    </h1>
  </section>

  <section class="card card--back">
    <div class="holder">
      <h2 class="holder__name">LUKE VARDEN LUKE VARDEN</h2>
      <p class="holder__credentials">BSc (kin), MPT, CAFCI, IMS</p>
    </div>

    <div class="divider"></div>

    <ul class="services">
      <li><span class="dot">•</span> Direct Billing</li>
      <li><span class="dot">•</span> Services including Physiotherapy</li>
      <li><span class="dot">•</span> IMS <span class="dot">•</span> Acupuncture</li>
    </ul>

    <ul class="contacts">
      <li>
        <svg viewBox="0 0 12 12" aria-hidden="true"><path fill="#29456b" d="M2.5 1l2 2.2-1 1.3c.7 1.5 1.9 2.7 3.4 3.4l1.3-1 2.2 2-1.2 1.6C5 10.2 1.8 7 .9 2.2z"/></svg>
        867-555-0142
      </li>
      <li>
        <svg viewBox="0 0 12 12" aria-hidden="true"><rect x="1" y="2.5" width="10" height="7" fill="none" stroke="#29456b" stroke-width="1.2"/><path d="M1 2.8l5 4 5-4" fill="none" stroke="#29456b" stroke-width="1.1"/></svg>
        VardenTherapy@postnest.ca
      </li>
      <li>
        <svg viewBox="0 0 12 12" aria-hidden="true"><circle cx="6" cy="6" r="5" fill="none" stroke="#29456b" stroke-width="1.1"/><ellipse cx="6" cy="6" rx="2.2" ry="5" fill="none" stroke="#29456b" stroke-width="0.9"/><path d="M1 6h10" stroke="#29456b" stroke-width="0.9"/></svg>
        www.VardenTherapy.ca
      </li>
      <li>
        <span class="social-dot"></span>
        VardenTherapy
      </li>
    </ul>

    <div class="slogan-band">Mobile Physiotherapy - Your Road To Recovery</div>
  </section>
</body>
</html>
```